Church Website with Home Page and Member Sermon Library

I am in need of an updated design for our church website. This will include 4 pages (outlined below). We are a conservative, evangelical, Christian church. The site should be modern and clean, while still reflecting our conservative values. I already have a logo for our church, and I want the site to incorporate the logo, and match the logo/branding. Stock photos are allowed if needed, but I have uploaded some images of our church and would prefer those images to be used if possible. Any stock photos used should not include any people in the photos (scenery, nature, buildings, animals, etc. are fine).

The site will need 4 pages: Home, Support Us (Donate), Login, and Recording Library.

Page 1: Home
The home page should include the following sections:

- Navigation: Should include links to each section of the home page plus a "listen live" link which will take the user to a live-streaming site and a "support us" link which will take the user to a support/donate page.

- Announcements: Can be either a banner or some other design, but there needs to be some way for us to post announcements for visitors to see. I'm open for creative ideas in this section, but would like it not to take up a lot of room on the page.

- About Us: Should include address, service times (see attached document), and information about the church.

- Pastor Bio: A section that introduces our pastor and gives a short bio about our pastor. Would like this section to include a picture of our pastor. Somewhere in this section I would like to include this Bible reference: "And I will give you pastors according to mine heart, which shall feed you with knowledge and understanding. Jer 3:15 LPW"

- Articles of Faith (What We Believe): This should include several sub-sections each with a heading, body, and possibly 1 or more scripture references. I have attached a document to the brief that includes our articles of faith. Feel free to be creative with this section in how you lay these out and format them.

- Support Us: A small section that explains what kind of support someone can give and a link to a donation page. The link can say something like "Support Us" or "Donate Now".

- Contact form: A contact form that allows the visitor to send us a message. The contact form should ask for name, email, phone, and message.

- Footer: A footer that will be displayed on all pages of the site. This should include at a minimum a link to the home page (or a link to each individual section in the home page if you prefer), a link to "listen live", a link to "support us", a link to "contact us" (or you can put the contact form directly in the footer if you prefer), the address, and a "member login" link.

Page 2: Support Us
The donation page should include a form the visitor can fill out to make a donation. We will embed a third party form later. For this design, please just mock out the design with a basic form asking for name, phone, and email.

Page 3: Login
The recording library (detailed below) will require members to login with a shared numeric code before accessing the page. We need a design for a login screen. The screen should include navigation/footer just like all other pages, but the body of the login page will consist only of a form that asks the user to enter the access code and then a "login" button.

Page 4: Recording Library

The library page is a member-only page that will require a shared, numeric pass code to access. On this page, members will be able to access a filterable list of past sermons. The page by default should display most recent sermons, but should also include a search form that allows the member to filter the sermon list to find a particular sermon. The search form should allow the user to select a filter type (e.g. Speaker name, date, event, etc.) and type in a value to search. They should be able to add multiple filters and remove filters that have been added. Each sermon that is displayed in the result list should include basic information such as title, date, speaker, tags, etc. along with a download icon, and an embedded audio player where they can click a play button to stream it on-demand. Each sermon should also have clickable tags associated with it that can be used to find related sermons.
Updates

I have uploaded several images of our church. Feel free to incorporate these into your design if possible.

Target Market(s)

Church Members

Industry/Entity Type

Religion

Number of Pages Required

4 page

Font styles to use
Sans Serif

Colors

Designer to choose colors to be used in the design.

Requirements
Must have
• Must incorporate the logo (attached)
Nice to have
• Would like the design to incorporate pictures of our church (attached) instead of stock photos if possible.
Should not have
• Please avoid an overly cluttered design. Stock photos used should not include any people in the photos.

```html
<!DOCTYPE html>
<html lang="en">
<head>
<meta charset="utf-8">
<title>Library – Grace Harbor Church</title>
<link href="https://fonts.googleapis.com/css2?family=Cinzel:wght@400;600;700&family=Montserrat:wght@400;500;600&display=swap" rel="stylesheet">
<style>
:root{
  --ink:#1c1f24;
  --footer:#20242b;
  --green:#7fa86a;
  --muted:#8a8f96;
  --line:#d9dcdf;
  --field:#f6f7f8;
  --white:#ffffff;
}
*{box-sizing:border-box;margin:0;padding:0}
html,body{width:707px;height:1200px;overflow:hidden;background:var(--white)}
body{font-family:'Montserrat',sans-serif;color:var(--ink);position:relative}
h1,h2,h3,h4{font-weight:400}

.hero{position:absolute;left:0;top:0;width:707px;height:250px;
  background:radial-gradient(ellipse at 50% 60%,#6a4a3a 0%,#3a2a26 35%,#16161b 80%)}
.hero-photo{position:absolute;inset:0}
.brand{position:absolute;left:26px;top:20px;display:flex;align-items:center;gap:8px;
  font-family:'Cinzel',serif;font-weight:600;font-size:13px;letter-spacing:2px;color:#8fb3a9}
.brand-dot{width:12px;height:12px;border-radius:50%;background:#8fb3a9}
.nav{position:absolute;right:34px;top:14px;display:flex;align-items:center;gap:18px;
  font-size:7.5px;font-weight:500;letter-spacing:.5px;color:var(--white)}
.btn{background:var(--green);color:var(--white);font-size:7.5px;font-weight:600;padding:5px 9px;letter-spacing:.5px;border:0;font-family:inherit}
.hero-title{position:absolute;left:0;right:0;top:140px;text-align:center;font-family:'Cinzel',serif;
  font-size:32px;letter-spacing:3px;color:var(--white)}
.hero-title::after{content:"";display:block;width:46px;height:1px;background:var(--white);margin:8px auto 0}

.sermons{position:absolute;left:101px;top:298px;width:505px}
.sermons-head{display:flex;justify-content:space-between;align-items:center;height:28px}
.sermons-title{font-family:'Cinzel',serif;font-size:20px;letter-spacing:1.5px}
.sort{display:flex;align-items:center;gap:8px;font-size:7px;color:#555}
.sort-box{width:64px;height:16px;border:1px solid var(--line);display:flex;align-items:center;justify-content:space-between;padding:0 7px;font-size:7px}

.filters{margin-top:12px;display:flex;align-items:center;gap:6px}
.filter-select,.filter-value{height:20px;border:1px solid var(--line);background:var(--field);font-size:7px;color:#666;display:flex;align-items:center;padding:0 8px}
.filter-select{width:90px;justify-content:space-between}
.filter-value{flex:1}
.filters .btn{height:20px;display:flex;align-items:center}
.active-filters{margin-top:7px;display:flex;gap:6px;align-items:center;font-size:6.5px;color:#666}
.chip{display:flex;align-items:center;gap:5px;border:1px solid var(--green);border-radius:10px;padding:3px 8px;color:var(--ink)}
.chip b{font-weight:600;color:var(--green)}
.clear{color:var(--muted);text-decoration:underline}

.grid{margin-top:14px;display:grid;grid-template-columns:248px 248px;column-gap:9px;row-gap:13px}
.card{position:relative;height:146px;overflow:hidden;color:var(--white)}
.card-photo{position:absolute;inset:0;background:linear-gradient(100deg,#4a2418 0%,#6b3a28 40%,#2b1d1a 75%,#141418 100%)}
.card-shade{position:absolute;left:0;right:0;bottom:0;height:60px;background:linear-gradient(transparent,rgba(0,0,0,.85))}
.download{position:absolute;right:10px;top:8px;font-size:6px;display:flex;gap:4px;align-items:center;opacity:.9}
.play{position:absolute;left:50%;top:40px;margin-left:-17px}
.card-info{position:absolute;left:10px;bottom:7px;right:10px}
.date{font-size:5.5px;opacity:.9}
.card-title{font-family:'Cinzel',serif;font-weight:700;font-size:7.5px;letter-spacing:1px;margin:3px 0 4px}
.speaker{display:flex;align-items:center;gap:5px;font-size:5.5px;opacity:.9}
.avatar{width:9px;height:9px;border-radius:50%;background:#c9b8a8}

.tags{position:absolute;left:101px;top:876px;width:505px}
.tags-title{font-family:'Cinzel',serif;font-size:8px;letter-spacing:1px;font-weight:600}
.tag-list{margin-top:12px;display:flex;flex-wrap:wrap;gap:8px 7px}
.tag{border:1px solid var(--line);border-radius:10px;padding:4px 10px;font-size:5.5px;color:#666}

.footer{position:absolute;left:0;top:1018px;width:707px;height:182px;background:var(--footer);color:#c5c8cc}
.footer-mark{position:absolute;left:60px;top:80px;font-family:'Cinzel',serif;font-size:14px;font-weight:600;letter-spacing:2px;color:#4a5a58}
.footer-col{position:absolute;top:40px;font-size:6px;line-height:1.9}
.footer-col h4{font-family:'Cinzel',serif;font-size:10px;letter-spacing:1.5px;color:var(--white);margin-bottom:8px}
.contact{left:246px}
.donation{left:427px;width:150px}
.donation .btn{display:inline-block;margin-top:10px}
.social{position:absolute;right:40px;top:156px;display:flex;gap:8px}
.social span{width:5px;height:5px;border-radius:50%;background:#9aa0a6}
.copyright{position:absolute;left:60px;top:154px;font-size:5.5px;color:#8a8f96}
</style>
</head>
<body>

<header class="hero">
  <div class="hero-photo" role="img" aria-label="Gothic cathedral interior with tall stained glass windows"></div>
  <div class="brand"><span class="brand-dot"></span>GRACE HARBOR</div>
  <nav class="nav"><span>HOME</span><span>LIBRARY</span><span class="btn">DONATE</span></nav>
  <h1 class="hero-title">LIBRARY</h1>
</header>

<main class="sermons">
  <div class="sermons-head">
    <h2 class="sermons-title">LIST OF PAST SERMONS</h2>
    <div class="sort">Sort sermons by: <div class="sort-box">Latest <span>▾</span></div></div>
  </div>

  <form class="filters">
    <div class="filter-select">Speaker name <span>▾</span></div>
    <div class="filter-value">Type a value to search…</div>
    <span class="btn">+ ADD FILTER</span>
    <span class="btn">SEARCH</span>
  </form>
  <div class="active-filters">
    <span>Active filters:</span>
    <span class="chip"><b>Speaker:</b> Mara Whitfield ✕</span>
    <span class="chip"><b>Event:</b> Sunday Service ✕</span>
    <span class="clear">Clear all</span>
  </div>

  <div class="grid">
    <article class="card">
      <div class="card-photo" role="img" aria-label="Preacher at the pulpit beside a cross"></div>
      <div class="card-shade"></div>
      <div class="download">Download <svg width="8" height="8" viewBox="0 0 8 8"><path d="M4 0v5M2 3l2 2 2-2M0 7h8" stroke="#fff" fill="none"/></svg></div>
      <svg class="play" width="34" height="34" viewBox="0 0 40 40"><circle cx="20" cy="20" r="19" fill="rgba(255,255,255,.75)"/><path d="M16 13l11 7-11 7z" fill="#555"/></svg>
      <div class="card-info"><div class="date">▣ Feb 12, 2023</div><div class="card-title">ULLAMCORPER FACILISI EGESTAS</div><div class="speaker"><span class="avatar"></span>by: Mara Whitfield</div></div>
    </article>
    <article class="card">
      <div class="card-photo" role="img" aria-label="Preacher at the pulpit beside a cross"></div>
      <div class="card-shade"></div>
      <div class="download">Download <svg width="8" height="8" viewBox="0 0 8 8"><path d="M4 0v5M2 3l2 2 2-2M0 7h8" stroke="#fff" fill="none"/></svg></div>
      <svg class="play" width="34" height="34" viewBox="0 0 40 40"><circle cx="20" cy="20" r="19" fill="rgba(255,255,255,.75)"/><path d="M16 13l11 7-11 7z" fill="#555"/></svg>
      <div class="card-info"><div class="date">▣ Feb 12, 2023</div><div class="card-title">ULLAMCORPER FACILISI EGESTAS</div><div class="speaker"><span class="avatar"></span>by: Mara Whitfield</div></div>
    </article>
    <article class="card">
      <div class="card-photo" role="img" aria-label="Preacher at the pulpit beside a cross"></div>
      <div class="card-shade"></div>
      <div class="download">Download <svg width="8" height="8" viewBox="0 0 8 8"><path d="M4 0v5M2 3l2 2 2-2M0 7h8" stroke="#fff" fill="none"/></svg></div>
      <svg class="play" width="34" height="34" viewBox="0 0 40 40"><circle cx="20" cy="20" r="19" fill="rgba(255,255,255,.75)"/><path d="M16 13l11 7-11 7z" fill="#555"/></svg>
      <div class="card-info"><div class="date">▣ Feb 12, 2023</div><div class="card-title">ULLAMCORPER FACILISI EGESTAS</div><div class="speaker"><span class="avatar"></span>by: Mara Whitfield</div></div>
    </article>
    <article class="card">
      <div class="card-photo" role="img" aria-label="Preacher at the pulpit beside a cross"></div>
      <div class="card-shade"></div>
      <div class="download">Download <svg width="8" height="8" viewBox="0 0 8 8"><path d="M4 0v5M2 3l2 2 2-2M0 7h8" stroke="#fff" fill="none"/></svg></div>
      <svg class="play" width="34" height="34" viewBox="0 0 40 40"><circle cx="20" cy="20" r="19" fill="rgba(255,255,255,.75)"/><path d="M16 13l11 7-11 7z" fill="#555"/></svg>
      <div class="card-info"><div class="date">▣ Feb 12, 2023</div><div class="card-title">ULLAMCORPER FACILISI EGESTAS</div><div class="speaker"><span class="avatar"></span>by: Mara Whitfield</div></div>
    </article>
    <article class="card">
      <div class="card-photo" role="img" aria-label="Preacher at the pulpit beside a cross"></div>
      <div class="card-shade"></div>
      <div class="download">Download <svg width="8" height="8" viewBox="0 0 8 8"><path d="M4 0v5M2 3l2 2 2-2M0 7h8" stroke="#fff" fill="none"/></svg></div>
      <svg class="play" width="34" height="34" viewBox="0 0 40 40"><circle cx="20" cy="20" r="19" fill="rgba(255,255,255,.75)"/><path d="M16 13l11 7-11 7z" fill="#555"/></svg>
      <div class="card-info"><div class="date">▣ Feb 12, 2023</div><div class="card-title">ULLAMCORPER FACILISI EGESTAS</div><div class="speaker"><span class="avatar"></span>by: Mara Whitfield</div></div>
    </article>
    <article class="card">
      <div class="card-photo" role="img" aria-label="Preacher at the pulpit beside a cross"></div>
      <div class="card-shade"></div>
      <div class="download">Download <svg width="8" height="8" viewBox="0 0 8 8"><path d="M4 0v5M2 3l2 2 2-2M0 7h8" stroke="#fff" fill="none"/></svg></div>
      <svg class="play" width="34" height="34" viewBox="0 0 40 40"><circle cx="20" cy="20" r="19" fill="rgba(255,255,255,.75)"/><path d="M16 13l11 7-11 7z" fill="#555"/></svg>
      <div class="card-info"><div class="date">▣ Feb 12, 2023</div><div class="card-title">ULLAMCORPER FACILISI EGESTAS</div><div class="speaker"><span class="avatar"></span>by: Mara Whitfield</div></div>
    </article>
  </div>
</main>

<section class="tags">
  <h3 class="tags-title">RELATED SERMONS TAG</h3>
  <div class="tag-list">
    <span class="tag">Ullamcorper facilisi</span><span class="tag">eu id tempus</span><span class="tag">in consectetur leo</span><span class="tag">elementum gravida</span><span class="tag">announ gravida</span>
    <span class="tag">in consectetur leo</span><span class="tag">elementum gravida</span><span class="tag">announ gravida</span>
  </div>
</section>

<footer class="footer">
  <div class="footer-mark">GRACE HARBOR</div>
  <div class="footer-col contact">
    <h4>CONTACT</h4>
    <p>◉ 418 Lantern Hill Road,<br>Maple Ridge, OH 44012</p>
    <p>✆ +1 555 204 7731</p>
    <p>✉ hello@graceharborchurch.org</p>
  </div>
  <div class="footer-col donation">
    <h4>DONATION</h4>
    <p>Aliquam at commodo venenatis quis nibh neque interdum molestie risus.</p>
    <span class="btn">DONATE</span>
  </div>
  <div class="copyright">Copyright 2023 Grace Harbor Church | All rights reserved</div>
  <div class="social"><span></span><span></span><span></span><span></span></div>
</footer>

</body>
</html>
```